New florist business website design

Number 1 want is an easy to navigate & check out website
Needs to be beautiful and eye catching as well.
This is an online only business (no shop front)
Rustic and blush pinks, neutrals, woods, leaves
Customers need to be able to go onto my website, select something they want to buy but have the option to use a drop down box to change colours of the flowers, or add notes to make changes to the arrangement

Industry/Entity Type

Florist

Coding

Coded - Design and coding required

Number of Pages Required

5+ page

Colors
f9d9e8
fff2ec
fffefc

Requirements
Must have
• Drop down menu to take you to other pages for Arrangements, bouquets, everlasting arrangements, gifts, contact
Be able to purchase and “add to basket”
Checkout page
Nice to have
• Be able to add my own photos once I’ve taken new ones
Should not have
• Tacky images or clip art

```html
<!DOCTYPE html>
<html lang="en">
<head>
<meta charset="utf-8">
<title>Fern &amp; Bloom – Florist</title>
<link href="https://fonts.googleapis.com/css2?family=Poppins:wght@300;400;500;600;700&display=swap" rel="stylesheet">
<style>
:root{
  --blush:#f9d9e8;
  --peach:#fff2ec;
  --cream:#fffefc;
  --sand:#fde4d0;
  --ink:#222222;
  --footer:#2f2f2f;
  --muted:#6b6b6b;
  --star:#f0a92e;
  --line:#e9dcd6;
}
*{box-sizing:border-box;margin:0;padding:0}
html,body{width:1200px;height:3081px;overflow:hidden}
body{background:var(--peach);font-family:'Poppins',sans-serif;color:var(--ink);position:relative}
.abs{position:absolute}
a{color:inherit;text-decoration:none}

/* top bar */
.help{left:111px;top:14px;font-size:14px;color:#444;display:flex;align-items:baseline;gap:12px}
.help strong{font-size:17px;font-weight:600;color:var(--ink);letter-spacing:.5px}
.account{right:208px;top:16px;font-size:14px;color:#555}
.account span{margin:0 8px}
.top-icons{right:112px;top:12px;display:flex;gap:16px}

/* nav */
.nav{left:111px;top:53px;width:977px;height:51px;background:#fff;box-shadow:0 2px 6px rgba(0,0,0,.08);font-size:14px;color:#333}
.nav ul{list-style:none;display:flex;position:absolute;top:16px;gap:28px}
.nav .left{left:31px}
.nav .right{right:36px;gap:20px}
.caret{font-size:10px;margin-left:4px}
.logo{left:531px;top:10px;width:136px;height:136px;border-radius:50%;background:var(--blush);border:3px solid #fff;display:flex;align-items:center;justify-content:center;font-size:17px;font-weight:400;color:#4a3b3f;z-index:3}

/* hero */
.hero{left:111px;top:104px;width:977px;height:557px;background:linear-gradient(90deg,#c9c9c9 0%,#e2e2e2 40%,#e9a05a 55%,#dd5a3a 65%,#d8d8d8 85%)}
.hero h1{position:absolute;left:64px;top:170px;font-size:76px;font-weight:700;color:#2a2a2a;letter-spacing:1px}
.hero p{position:absolute;left:64px;top:278px;font-size:22px;font-weight:500;color:#2a2a2a}
.btn{display:inline-block;background:var(--sand);color:var(--ink);font-weight:500}
.hero .btn{position:absolute;left:64px;top:319px;width:113px;height:40px;line-height:40px;text-align:center;font-size:18px}
.arrow{top:368px}

/* promo */
.promo{left:111px;top:701px;width:977px;height:410px;display:flex}
.promo .img-roses{width:253px;background:linear-gradient(135deg,#b8141c,#e22a2a,#8c0c12)}
.promo .img-florist{width:256px;background:linear-gradient(180deg,#9fb3c4,#2d3440 45%,#e7c3c2 65%,#2a2e36)}
.promo .panel{background:#000;color:#fff;padding:120px 0 0 20px}
.promo .p1{width:233px}
.promo .p2{width:235px}
.promo small{font-size:14px}
.promo h2{font-size:22px;font-weight:600;line-height:35px;margin-top:12px}
.promo .btn{margin-top:24px;height:41px;line-height:41px;padding:0 14px;font-size:17px}

/* decor */
.decor{border-radius:50%;filter:blur(2px)}

/* products */
.section-title{left:0;width:1200px;top:1185px;text-align:center;font-size:19px;letter-spacing:4px;font-weight:500}
.card{background:#fff;border:1px solid var(--line);width:237px;height:322px}
.card .ph{position:absolute;left:9px;top:9px;width:219px;height:226px}
.card h3{position:absolute;left:0;width:100%;top:256px;text-align:center;font-size:14px;font-weight:400}
.card .price{position:absolute;left:0;width:100%;top:287px;text-align:center;font-size:14px}
.discover{left:514px;top:1924px;width:171px;height:41px;line-height:41px;text-align:center;font-size:17px}

/* features */
.feature{background:#fff;border:1px solid var(--line);width:316px;height:278px;overflow:hidden}
.feature .stars{position:absolute;left:18px;top:38px;font-size:17px;color:var(--star);letter-spacing:2px}
.feature .stars span{color:#555;font-size:17px;margin-left:4px}
.feature .eyebrow{position:absolute;left:18px;top:94px;font-size:15px;letter-spacing:3px;color:#444}
.feature h3{position:absolute;left:18px;top:118px;font-size:22px;font-weight:400;line-height:34px;color:#444}
.feature .mini{position:absolute;left:18px;top:213px;background:var(--blush);font-size:13px;padding:2px 13px;color:#444}
.feature .ph{position:absolute;right:0;top:40px;width:150px;height:210px;border-radius:40% 0 0 40%}

/* newsletter */
.newsletter{left:111px;top:2339px;width:977px;height:218px;background:#fff;box-shadow:0 4px 12px rgba(0,0,0,.1);overflow:hidden}
.newsletter h2{position:absolute;left:41px;top:38px;font-size:37px;font-weight:600;color:#333}
.newsletter p{position:absolute;left:41px;top:96px;width:500px;font-size:16px;line-height:25px;color:#333}
.newsletter .field{position:absolute;left:41px;top:145px;width:362px;height:39px;border:1px solid #ccc;font-size:13px;color:#888;padding:10px 16px}
.newsletter .submit{position:absolute;left:402px;top:143px;width:152px;height:43px;background:var(--blush);font-size:21px;font-weight:600;text-align:center;line-height:43px;box-shadow:0 2px 5px rgba(0,0,0,.15)}
.newsletter .ph{position:absolute;right:0;top:0;width:430px;height:218px;background:linear-gradient(90deg,#fff 0%,#e9d5cf 30%,#c6426e 65%,#e7a3b8 85%,#d9d6d6)}

/* benefits */
.benefits{left:111px;top:2622px;width:977px;height:129px;background:var(--blush);border:4px solid #fff;z-index:2}
.benefit{position:absolute;top:26px;display:flex;gap:18px}
.benefit .icon{width:70px;height:70px;border-radius:50%;background:#fff;box-shadow:0 2px 6px rgba(0,0,0,.15);display:flex;align-items:center;justify-content:center;flex:none}
.benefit h4{font-size:16px;font-weight:400;color:#333;margin-top:6px}
.benefit p{font-size:11px;color:#666;width:190px;line-height:17px;margin-top:4px}

/* footer */
.footer{left:0;top:2711px;width:1200px;height:370px;background:var(--footer);color:#fff}
.fcol{position:absolute;top:92px}
.fcol h5{font-size:17px;font-weight:400;letter-spacing:.5px;margin-bottom:14px}
.fcol li{list-style:none;font-size:13px;line-height:25px}
.fcol .need{font-size:17px;margin-top:8px}
.fcol .phone{font-size:29px;font-weight:300;letter-spacing:.5px;margin-top:2px}
.fcol .social{font-size:17px;margin-top:16px}
.socials{display:flex;gap:6px;margin-top:10px}
.socials span{width:29px;height:29px;border-radius:50%;background:#ddd;display:block}
.rule{position:absolute;left:111px;top:300px;width:977px;height:1px;background:#555}
.copy{position:absolute;left:111px;top:324px;font-size:14px}
.cards{position:absolute;left:868px;top:322px;display:flex;gap:6px}
.cards span{width:24px;height:15px;background:#fff;border-radius:2px;display:block}
.code{position:absolute;right:30px;top:326px;font-size:14px;color:#ccc}
</style>
</head>
<body>

<div class="abs help">Need A Help? <strong>555-014-2290</strong></div>
<div class="abs account">My Account<span>|</span>Log In</div>
<div class="abs top-icons">
  <svg width="22" height="22" viewBox="0 0 24 24" fill="none" stroke="#333" stroke-width="1.6"><circle cx="12" cy="8" r="4.5"/><path d="M3 22c0-5 4-8 9-8s9 3 9 8z"/></svg>
  <svg width="22" height="22" viewBox="0 0 24 24" fill="none" stroke="#333" stroke-width="1.6"><path d="M12 21l-8.5-8.5a5 5 0 017-7L12 7l1.5-1.5a5 5 0 017 7z"/></svg>
</div>

<nav class="abs nav">
  <ul class="left">
    <li>Home</li>
    <li>Arrangements<span class="caret">&#8964;</span></li>
    <li>Bouquets<span class="caret">&#8964;</span></li>
  </ul>
  <ul class="right">
    <li>Everlasting Arrangements<span class="caret">&#8964;</span></li>
    <li>Gifts<span class="caret">&#8964;</span></li>
    <li>Contact</li>
  </ul>
</nav>
<div class="abs logo">Fern &amp; Bloom</div>

<section class="abs hero" role="img" aria-label="Bright bouquet of dahlias and gerberas in a glass vase beside a white chair and mug">
  <h1>Fern &amp; Bloom</h1>
  <p>A new Florist Business.</p>
  <a class="btn">Shop Now</a>
</section>
<svg class="abs arrow" style="left:36px" width="50" height="30" viewBox="0 0 50 30" fill="none" stroke="#111" stroke-width="2.5"><path d="M48 15H3M15 3L3 15l12 12"/></svg>
<svg class="abs arrow" style="left:1116px" width="50" height="30" viewBox="0 0 50 30" fill="none" stroke="#111" stroke-width="2.5"><path d="M2 15h45M35 3l12 12-12 12"/></svg>

<section class="abs promo">
  <div class="img-roses" role="img" aria-label="Close-up of red roses"></div>
  <div class="panel p1"><small>New Arrivals</small><h2>Everlasting<br>Arrangements</h2><a class="btn">Shop Now</a></div>
  <div class="img-florist" role="img" aria-label="Florist in an apron holding a pastel bouquet"></div>
  <div class="panel p2"><small>Popular</small><h2>Best<br>Bouquets</h2><a class="btn">Shop Now</a></div>
</section>

<div class="abs decor" style="left:-20px;top:1080px;width:240px;height:240px;background:radial-gradient(circle,#e25b2a 0%,#f0c030 35%,#6d9a3a 60%,rgba(109,154,58,0) 72%)" role="img" aria-label="Tropical flower arrangement"></div>
<div class="abs decor" style="left:1000px;top:1790px;width:230px;height:340px;background:radial-gradient(ellipse,#9b2441 0%,#d9a1b0 35%,#6e8d7a 55%,rgba(110,141,122,0) 70%)" role="img" aria-label="Roses and eucalyptus arrangement"></div>
<div class="abs decor" style="left:-30px;top:2460px;width:240px;height:260px;background:radial-gradient(circle,#e0263e 0%,#f2b92c 35%,#e63a62 55%,rgba(230,58,98,0) 70%)" role="img" aria-label="Bunch of colourful tulips"></div>

<h2 class="abs section-title">MOST POPULAR PRODUCTS</h2>

<div class="abs card" style="left:114px;top:1237px"><div class="ph" role="img" aria-label="Pink and peach rose bouquet" style="background:linear-gradient(#ece6e6,#e88b8f 50%,#ece6e6)"></div><h3>Est qui dolorem ipsum</h3><div class="price">$250</div></div>
<div class="abs card" style="left:359px;top:1237px"><div class="ph" role="img" aria-label="Mixed roses in a glass vase" style="background:linear-gradient(#ece6e6,#e25d6c 40%,#ece6e6)"></div><h3>Est qui dolorem ipsum</h3><div class="price">$250</div></div>
<div class="abs card" style="left:604px;top:1237px"><div class="ph" role="img" aria-label="Hydrangea and iris arrangement in a vase" style="background:linear-gradient(#ece6e6,#b9d27a 45%,#ece6e6)"></div><h3>Est qui dolorem ipsum</h3><div class="price">$250</div></div>
<div class="abs card" style="left:850px;top:1237px"><div class="ph" role="img" aria-label="Cream rose bouquet" style="background:linear-gradient(#ece6e6,#efd6c8 50%,#ece6e6)"></div><h3>Est qui dolorem ipsum</h3><div class="price">$250</div></div>

<div class="abs card" style="left:114px;top:1569px"><div class="ph" role="img" aria-label="Yellow and purple wildflower stem" style="background:linear-gradient(#ece6e6,#d7cf8f 50%,#ece6e6)"></div><h3>Est qui dolorem ipsum</h3><div class="price">$250</div></div>
<div class="abs card" style="left:359px;top:1569px"><div class="ph" role="img" aria-label="Bright yellow and orange rose bouquet" style="background:linear-gradient(#ece6e6,#f2a83a 50%,#ece6e6)"></div><h3>Est qui dolorem ipsum</h3><div class="price">$250</div></div>
<div class="abs card" style="left:604px;top:1569px"><div class="ph" role="img" aria-label="Purple and white lily bouquet" style="background:linear-gradient(#ece6e6,#a66bc0 50%,#ece6e6)"></div><h3>Est qui dolorem ipsum</h3><div class="price">$250</div></div>
<div class="abs card" style="left:850px;top:1569px"><div class="ph" role="img" aria-label="Pink peonies in a glass vase" style="background:linear-gradient(#ece6e6,#e37aa6 45%,#ece6e6)"></div><h3>Est qui dolorem ipsum</h3><div class="price">$250</div></div>

<a class="abs btn discover">Discover All</a>

<div class="abs feature" style="left:111px;top:2022px">
  <div class="ph" role="img" aria-label="Pastel peony bouquet with greenery" style="background:linear-gradient(135deg,#fff,#f4b6c4 50%,#a9c98a)"></div>
  <div class="stars">★★★★★<span>(256)</span></div>
  <div class="eyebrow">FERN &amp; BLOOM</div>
  <h3>Neque porro<br>quisquam</h3>
  <span class="mini">Shop Now</span>
</div>
<div class="abs feature" style="left:441px;top:2022px">
  <div class="ph" role="img" aria-label="Red rose arrangement in a gift box" style="background:linear-gradient(135deg,#fff,#d92a2e 50%,#b3121a)"></div>
  <div class="stars">★★★★★<span>(256)</span></div>
  <div class="eyebrow">FERN &amp; BLOOM</div>
  <h3>Neque porro<br>quisquam</h3>
  <span class="mini">Shop Now</span>
</div>
<div class="abs feature" style="left:771px;top:2022px">
  <div class="ph" role="img" aria-label="Red and pink mixed bouquet" style="background:linear-gradient(135deg,#fff,#e0485a 50%,#6f8f56)"></div>
  <div class="stars">★★★★★<span>(256)</span></div>
  <div class="eyebrow">BOUQUETS</div>
  <h3>Neque porro<br>quisquam</h3>
  <span class="mini">Shop Now</span>
</div>

<section class="abs newsletter">
  <div class="ph" role="img" aria-label="Woman smelling a pink bouquet"></div>
  <h2>Sign Up Our newsletter</h2>
  <p>Neque porro quisquam est qui dolorem ipsum quia dolor sit amet, consectetur, adipisci velit...</p>
  <div class="field">Enter Your Email</div>
  <div class="submit">Submit</div>
</section>

<footer class="abs footer">
  <div class="fcol" style="left:111px"><h5>ABOUT</h5><ul><li>About Us</li><li>Careers</li><li>Stories</li><li>Press</li><li>Wholesale</li></ul></div>
  <div class="fcol" style="left:312px"><h5>HELP</h5><ul><li>Payments</li><li>Shipping</li><li>Cancellation &amp; Returns</li><li>FAQ</li><li>Report Infringement</li></ul></div>
  <div class="fcol" style="left:569px"><h5>POLICY</h5><ul><li>Return Policy</li><li>Terms Of Use</li><li>Security</li><li>Privacy</li><li>Sitemap</li><li>EPR Compliance</li></ul></div>
  <div class="fcol" style="left:868px"><h5>QUICK HELPS</h5>
    <div class="need">NEED A HELP?</div>
    <div class="phone">+012 555 01840</div>
    <div class="social">SOCIAL</div>
    <div class="socials"><span></span><span></span><span></span><span></span></div>
  </div>
  <div class="rule"></div>
  <div class="copy">Copyright © 2021 Fern &amp; Bloom - All Rights Reserved.</div>
  <div class="cards"><span></span><span></span><span></span><span></span><span></span><span></span><span></span></div>
  <div class="code">C24</div>
</footer>

<section class="abs benefits">
  <div class="benefit" style="left:20px">
    <div class="icon"><svg width="36" height="36" viewBox="0 0 24 24" fill="none" stroke="#555" stroke-width="1.3"><circle cx="12" cy="9" r="6"/><path d="M8 14l-3 7 3-1 2 2 2-4M16 14l3 7-3-1-2 2-2-4"/></svg></div>
    <div><h4>100% Neque porro</h4><p>Lorem ipsum is simply dummy text of the printing and</p></div>
  </div>
  <div class="benefit" style="left:356px">
    <div class="icon"><svg width="38" height="38" viewBox="0 0 24 24" fill="none" stroke="#555" stroke-width="1.3"><rect x="2" y="7" width="12" height="9"/><path d="M14 10h4l3 3v3h-7z"/><circle cx="6" cy="17.5" r="1.6"/><circle cx="17" cy="17.5" r="1.6"/></svg></div>
    <div><h4>Free delivery</h4><p>Lorem ipsum is simply dummy text of the printing and t</p></div>
  </div>
  <div class="benefit" style="left:682px">
    <div class="icon"><svg width="36" height="36" viewBox="0 0 24 24" fill="none" stroke="#555" stroke-width="1.3"><circle cx="14" cy="8" r="5"/><path d="M12 10l4-4M12.3 6.5h.1M15.8 9.5h.1M2 15h4l4 2h5l4-3M6 20h8l6-4"/></svg></div>
    <div><h4>Cash Back Guarantee</h4><p>Lorem ipsum is simply dummy text printing and typesetting industry.</p></div>
  </div>
</section>

</body>
</html>
```